Varnex Consulting Business card design.

See our website www.varnexconsulting.example which will give you a good idea of what we are about. The font is called 'Play'.

I'd like a standout business card in keeping with the themes and branding on the website

Target Market(s)

professionals. HR directors

Industry/Entity Type

Business

Contact Information for Business Card

Varnex Consulting PO Box 3172 Merrowdale NSW 2291 1300 485 193 Gavin Threlkeld Principal email: career@varnexconsulting.example ABN: 71203948865

Font styles to use
Other font styles liked:
• Play

Requirements
Must have
• Must have same design colours and branding as website.
• On back I'd prefer a list of the things we do which appears below the name at the header on the website

```html
<!DOCTYPE html>
<html lang="en">
<head>
<meta charset="utf-8">
<title>Varnex Consulting – Business Card</title>
<link rel="stylesheet" href="https://fonts.googleapis.com/css2?family=Play:wght@400;700&family=Arimo:wght@400;700&display=swap">
<style>
  :root {
    --page-bg: #e9e7e3;
    --navy-deep: #081a2b;
    --navy: #12304a;
    --navy-mid: #1d3f5c;
    --accent-blue: #2a9be0;
    --light-blue: #5fb6ea;
    --ink: #111c28;
    --text-grey: #3b3f44;
    --card-white: #ffffff;
    --card-fade: #eceef0;
  }
  * { box-sizing: border-box; margin: 0; padding: 0; }
  html, body {
    width: 1200px; height: 950px; overflow: hidden;
    background: var(--page-bg);
  }
  .canvas { position: relative; width: 1200px; height: 950px; }

  .card {
    position: absolute; left: 230px;
    width: 740px; height: 423px;
    border-radius: 4px; overflow: hidden;
    box-shadow: 0 8px 24px rgba(0,0,0,0.18);
  }

  /* Back of card */
  .card-back {
    top: 35px;
    background: linear-gradient(120deg, var(--navy-deep) 0%, var(--navy) 60%, var(--navy-mid) 100%);
  }
  .card-back .wordmark {
    position: absolute; left: 0; right: 0; top: 150px;
    text-align: center;
    font-family: "Play", sans-serif; font-size: 54px; letter-spacing: 4px;
    color: var(--card-white);
  }
  .services {
    position: absolute; right: 60px; top: 250px;
    font-family: "Arimo", sans-serif; font-size: 19px; letter-spacing: 0.5px;
    color: #c9d3dc;
  }
  .services .sep { color: var(--accent-blue); margin: 0 8px; }

  /* Front of card */
  .card-front {
    top: 492px;
    background: linear-gradient(160deg, var(--card-white) 40%, var(--card-fade) 100%);
  }
  .card-front .wordmark {
    position: absolute; left: 50px; top: 38px;
    font-family: "Play", sans-serif; font-size: 58px; letter-spacing: 4px;
    color: var(--navy-deep);
  }
  .person { position: absolute; left: 50px; top: 172px; width: 250px; text-align: right; }
  .person-name {
    font-family: "Arimo", sans-serif; font-weight: 700; font-size: 23px;
    color: var(--ink);
  }
  .person-role {
    margin-top: 4px;
    font-family: "Arimo", sans-serif; font-size: 19px; color: var(--accent-blue);
  }
  .divider {
    position: absolute; left: 325px; top: 165px;
    width: 1px; height: 120px; background: #9aa2aa;
  }
  .contact {
    position: absolute; left: 350px; top: 168px;
    font-family: "Arimo", sans-serif; font-size: 19px; line-height: 27px;
    color: var(--text-grey);
  }
  .contact-row { display: flex; align-items: center; gap: 9px; }
  .contact-row svg { width: 18px; height: 18px; fill: var(--ink); flex: none; }

  .band-line-top {
    position: absolute; left: 0; right: 0; top: 306px;
    height: 3px; background: var(--light-blue);
  }
  .band {
    position: absolute; left: 0; right: 0; top: 318px; height: 66px;
    background: linear-gradient(90deg, var(--navy-deep) 0%, var(--navy) 70%, var(--navy-mid) 100%);
  }
  .band-line-bottom {
    position: absolute; left: 0; right: 0; top: 390px;
    height: 3px; background: var(--light-blue);
  }
  .website {
    position: absolute; left: 50px; top: 20px;
    font-family: "Arimo", sans-serif; font-size: 21px; letter-spacing: 2px;
    color: #dfe7ee;
  }
</style>
</head>
<body>
<main class="canvas">

  <section class="card card-back" aria-label="Business card back">
    <div class="wordmark">VARNEX CONSULTING</div>
    <div class="services">Career Coaching<span class="sep">|</span>Leadership<span class="sep">|</span>Outplacement</div>
  </section>

  <section class="card card-front" aria-label="Business card front">
    <div class="wordmark">VARNEX CONSULTING</div>

    <div class="person">
      <div class="person-name">Gavin Threlkeld</div>
      <div class="person-role">Principal</div>
    </div>

    <div class="divider"></div>

    <div class="contact">
      <div>PO Box 3172 Merrowdale</div>
      <div>NSW 2291</div>
      <div class="contact-row">
        <svg viewBox="0 0 24 24" aria-hidden="true"><path d="M6.6 10.8a15.1 15.1 0 0 0 6.6 6.6l2.2-2.2a1 1 0 0 1 1-.25 11.4 11.4 0 0 0 3.6.57 1 1 0 0 1 1 1V20a1 1 0 0 1-1 1A17 17 0 0 1 3 4a1 1 0 0 1 1-1h3.5a1 1 0 0 1 1 1c0 1.25.2 2.45.57 3.57a1 1 0 0 1-.25 1z"/></svg>
        <span>1300 485 193</span>
      </div>
      <div class="contact-row">
        <svg viewBox="0 0 24 24" aria-hidden="true"><path d="M2 5h20v14H2z M3.5 6.5 12 13l8.5-6.5" fill="none" stroke="#111c28" stroke-width="2"/><path d="M2 5h20v2l-10 7L2 7z"/></svg>
        <span>career@varnexconsulting.example</span>
      </div>
    </div>

    <div class="band-line-top"></div>
    <div class="band">
      <div class="website">www.varnexconsulting.example</div>
    </div>
    <div class="band-line-bottom"></div>
  </section>

</main>
</body>
</html>
```